QVR business card

Need a business card for a company that provides instructional design and elearning development services. The website is here: http://quorvane.studio/

I'm attaching a current logo, as well as the old business card design. While I like to keep it clean, the old design is too simplistic for my liking. The only idea I want to reuse from the old design is placing industry jargon on the back of the card, just need a better way to present it. But if you have other ideas for the back--feel free to experiment.

Please use the colors complementary to the color we have on the website. Thank you!

```html
<!DOCTYPE html>
<html lang="en">
<head>
<meta charset="utf-8">
<title>QVR business card</title>
<link href="https://fonts.googleapis.com/css2?family=Roboto+Condensed:wght@400;700&family=Ubuntu:wght@400;500&display=swap" rel="stylesheet">
<style>
  :root {
    --backdrop: #8e8e8e;
    --paper: #f2f3f3;
    --teal: #1a9f9a;
    --teal-deep: #17938e;
    --gold: #bfae72;
    --ink: #454545;
    --service-word: #e3ecea;
  }
  * { margin: 0; padding: 0; box-sizing: border-box; }
  html, body {
    width: 1105px;
    height: 1200px;
    overflow: hidden;
    background: var(--backdrop);
  }
  .card {
    position: absolute;
    left: 179px;
    width: 747px;
    height: 427px;
  }
  .card--front { top: 119px; background: var(--paper); }
  .card--back { top: 637px; background: var(--teal); }

  .brand {
    position: absolute;
    left: 40px;
    top: 0;
    display: flex;
    align-items: flex-end;
    gap: 14px;
  }
  .brand__mark {
    width: 56px;
    height: 56px;
    background: var(--teal);
  }
  .brand__name {
    font-family: "Ubuntu", sans-serif;
    font-weight: 500;
    font-size: 54px;
    line-height: 1;
    color: var(--gold);
    transform: translateY(14px);
  }

  .contact {
    position: absolute;
    left: 44px;
    top: 296px;
    list-style: none;
    font-family: "Ubuntu", sans-serif;
    font-size: 18px;
    color: var(--ink);
  }
  .contact__item {
    display: flex;
    align-items: center;
    gap: 10px;
    height: 29px;
  }
  .contact__icon { width: 16px; height: 16px; flex: none; }

  .person {
    position: absolute;
    right: 45px;
    top: 316px;
    text-align: right;
    font-family: "Ubuntu", sans-serif;
  }
  .person__name { font-size: 24px; color: var(--teal-deep); line-height: 1.2; }
  .person__role { font-size: 18px; color: var(--gold); line-height: 1.3; }

  .services { display: block; width: 747px; height: 427px; }
  .services text { fill: var(--service-word); }
  .services .cond { font-family: "Roboto Condensed", sans-serif; font-weight: 400; }
  .services .cond-bold { font-family: "Roboto Condensed", sans-serif; font-weight: 700; }
  .services .wide { font-family: "Ubuntu", sans-serif; font-weight: 400; }
  .services .wide-bold { font-family: "Ubuntu", sans-serif; font-weight: 500; }
</style>
</head>
<body>
  <section class="card card--front" aria-label="Business card front">
    <div class="brand">
      <span class="brand__mark"></span>
      <span class="brand__name">QVR</span>
    </div>

    <ul class="contact">
      <li class="contact__item">
        <svg class="contact__icon" viewBox="0 0 16 16" aria-hidden="true"><path fill="#1a9f9a" d="M3.2 1.2l2.4-.4 1.4 3.4-1.6 1.3c.8 1.8 2.1 3.1 3.9 3.9l1.3-1.6 3.4 1.4-.4 2.4c-.2.9-1 1.5-1.9 1.4C6.3 12.6 2.4 8.7 1.8 3.1c-.1-.9.5-1.7 1.4-1.9z"/></svg>
        <span>555-013-2468</span>
      </li>
      <li class="contact__item">
        <svg class="contact__icon" viewBox="0 0 16 16" aria-hidden="true"><rect x="1" y="3" width="14" height="10" fill="#1a9f9a"/><path d="M1.5 3.5L8 9l6.5-5.5" fill="none" stroke="#f2f3f3" stroke-width="1.3"/></svg>
        <span>dmarsh@quorvane.studio</span>
      </li>
      <li class="contact__item">
        <svg class="contact__icon" viewBox="0 0 16 16" aria-hidden="true"><circle cx="8" cy="8" r="7" fill="#1a9f9a"/><path d="M1.5 8h13M8 1c-2.5 2.5-2.5 11.5 0 14M8 1c2.5 2.5 2.5 11.5 0 14" fill="none" stroke="#f2f3f3" stroke-width="1"/></svg>
        <span>www.Quorvane.Studio</span>
      </li>
    </ul>

    <div class="person">
      <p class="person__name">Daniel Marsh</p>
      <p class="person__role">CEO/Founder</p>
    </div>
  </section>

  <section class="card card--back" aria-label="Business card back">
    <svg class="services" viewBox="0 0 747 427">
      <text class="cond-bold" x="14" y="50" font-size="42" textLength="270" lengthAdjust="spacingAndGlyphs">NEEDS ANALYSIS</text>
      <text class="cond" x="296" y="50" font-size="42" textLength="437" lengthAdjust="spacingAndGlyphs">STORYBOARDS ONBOARDING</text>

      <text class="wide" x="14" y="108" font-size="50" textLength="719" lengthAdjust="spacingAndGlyphs">MICROLEARNING PODCASTS</text>

      <text class="cond-bold" x="14" y="162" font-size="42" textLength="396" lengthAdjust="spacingAndGlyphs">ACCESSIBILITY AUDITS</text>
      <text class="cond" x="422" y="162" font-size="42" textLength="311" lengthAdjust="spacingAndGlyphs">QUIZ &amp; SURVEY BANKS</text>

      <text class="wide-bold" x="14" y="236" font-size="66" textLength="719" lengthAdjust="spacingAndGlyphs">LET'S BUILD IT.</text>

      <text class="cond" x="14" y="292" font-size="44" textLength="222" lengthAdjust="spacingAndGlyphs">SIMULATIONS</text>
      <text class="cond-bold" x="248" y="292" font-size="44" textLength="485" lengthAdjust="spacingAndGlyphs">PERFORMANCE SUPPORT</text>

      <text class="wide" x="14" y="350" font-size="46" textLength="719" lengthAdjust="spacingAndGlyphs">VIDEO SCRIPTS CAPTIONS</text>

      <text class="cond-bold" x="14" y="408" font-size="42" textLength="330" lengthAdjust="spacingAndGlyphs">LEARNER JOURNEYS</text>
      <text class="cond" x="356" y="408" font-size="42" textLength="377" lengthAdjust="spacingAndGlyphs">TRAINING ANALYTICS</text>
    </svg>
  </section>
</body>
</html>
```